Building company buisness cards

We are looking for a sharp modern new look for our business cards.
We are a New Zealand based company that specialises in house and land packages.
We have attached a photo of the current logo and would like to see if it can be improved somehow if needed.
We are open to any colours but we have chosen green at this stage.
Feel free to change the font and make the logo smarter looking.
Play with the colours and see what looks best.

We want a card that looks so good know one will want to throw it away!

Target Market(s)

Home buyers

Industry/Entity Type

Building

Contact Information for Business Card

Derek Tolvane
0217394062
dtolvane@quillmarkhomesteads.co.nz
quillmarkhomesteads.co.nz

Font styles to use
Serif
Sans Serif

Colors

Designer to choose colors to be used in the design.

Requirements
Must have
• Logo and company name on one side, details on the other side
Nice to have
• Color codes for the original green are HEX #4a8028, RGB(74,128,40), CMYK(42,0,69,50)
• Round corners, Raised and/or spot UV

```html
<!DOCTYPE html>
<html lang="en">
<head>
<meta charset="utf-8">
<title>Quillmark Homesteads – Business Card</title>
<link href="https://fonts.googleapis.com/css2?family=Open+Sans:wght@400&display=swap" rel="stylesheet">
<style>
  :root {
    --bg: #ececea;
    --paper: #ffffff;
    --green: #1f9a1b;
    --green-bright: #22c10a;
    --ink: #111111;
  }
  * { margin: 0; padding: 0; box-sizing: border-box; }
  html, body { width: 1200px; height: 1024px; overflow: hidden; }
  body {
    background: var(--bg);
    font-family: "Open Sans", Arial, sans-serif;
    display: flex;
    flex-direction: column;
    align-items: center;
    justify-content: center;
    gap: 40px;
  }
  .card {
    position: relative;
    width: 800px;
    height: 457px;
    background: var(--paper);
    border-radius: 6px;
    overflow: hidden;
    box-shadow: 0 2px 8px rgba(0,0,0,0.12);
  }
  .card-shapes { position: absolute; inset: 0; }
  .brand {
    position: absolute;
    left: 40px;
    top: 205px;
    width: 300px;
  }
  .brand-name {
    color: var(--green);
    font-weight: 400;
    font-size: 24px;
    line-height: 1.2;
    white-space: nowrap;
  }
  .holder-name {
    position: absolute;
    right: 120px;
    top: 118px;
    font-size: 24px;
    color: var(--ink);
    font-weight: 400;
  }
  .contact-list {
    position: absolute;
    right: 40px;
    top: 190px;
    list-style: none;
    text-align: right;
  }
  .contact-list li {
    display: flex;
    justify-content: flex-end;
    align-items: center;
    gap: 12px;
    color: var(--paper);
    font-size: 15px;
    line-height: 30px;
  }
  .contact-icon {
    width: 18px;
    height: 18px;
    background: var(--ink);
    display: inline-flex;
    align-items: center;
    justify-content: center;
  }
</style>
</head>
<body>

  <section class="card card-front">
    <svg class="card-shapes" viewBox="0 0 800 457" width="800" height="457" aria-hidden="true">
      <polygon points="300,0 800,0 800,457 470,457" fill="var(--green)"/>
      <polygon points="386,230 470,457 425,457 352,268" fill="var(--ink)"/>
    </svg>

    <div class="brand">
      <div class="brand-name">Quillmark Homesteads</div>
    </div>

    <div class="holder-name">Derek Tolvane</div>

    <ul class="contact-list">
      <li>0217394062
        <span class="contact-icon">
          <svg width="12" height="12" viewBox="0 0 12 12"><path d="M2.5 1 L4.5 1 L5 3.5 L3.8 4.3 Q4.8 6.8 7.7 8.2 L8.5 7 L11 7.5 L11 9.5 Q11 11 9.5 11 Q1 10 1 2.5 Q1 1 2.5 1 Z" fill="#fff"/></svg>
        </span>
      </li>
      <li>dtolvane@quillmarkhomesteads.co.nz
        <span class="contact-icon">
          <svg width="12" height="10" viewBox="0 0 12 10"><rect x="0.5" y="0.5" width="11" height="9" fill="none" stroke="#fff"/><path d="M0.5 0.5 L6 5.5 L11.5 0.5" fill="none" stroke="#fff"/></svg>
        </span>
      </li>
      <li>quillmarkhomesteads.co.nz
        <span class="contact-icon">
          <svg width="12" height="12" viewBox="0 0 12 12"><circle cx="6" cy="6" r="5" fill="none" stroke="#fff"/><ellipse cx="6" cy="6" rx="2.2" ry="5" fill="none" stroke="#fff"/><line x1="1" y1="6" x2="11" y2="6" stroke="#fff"/></svg>
        </span>
      </li>
    </ul>
  </section>

  <section class="card card-back">
    <svg class="card-shapes" viewBox="0 0 800 457" width="800" height="457" aria-hidden="true">
      <polygon points="470,457 520,330 690,330 760,390 800,390 800,457" fill="var(--green-bright)"/>
      <rect x="0" y="451" width="800" height="6" fill="var(--green)"/>
    </svg>
  </section>

</body>
</html>
```